Traineeship Flyer Design Project

Requirements:
• 1 x A4 page flyer (double sided)
1st page; target market 15-19 yr old, looking for young/fresh, exciting, eye catching
2nd page: same look/feel – target market – parents/person to determine if there is value to devoting energy to this qualification (potentially less busy in design)
• Use of high quality logos: 1. Valtrexo 2. Nationally recognised training logo
Ideally wanting to keep amount of copy to the page layout as attached, although designer is free to interpret the layout of copy on each page, although Valtrexo will accept alternative presentation if designer sees new way to combine information
• Valtrexo does not have a set colour palette so there are no restrictions/guidelines to follow
Updates
Hi, All files including brief and logos have now been updated.
Reason: Hi everyone
Please refer to design submission below for the only design that was deemed to cover off on the brief as the starting point - in regards to producing a design that appeals to target market of young person (15-19) in regards to self selecting to take up further study
Hi everyone
Can you please view the 3 remaining designs that are in contention (out of 30+ submitted) - Design 1528020 ; 1510098; 1510087; I will be providing additional feedback to these designers, as that come closer to the mark of appealing to younger "potential trainee" - the collateral needs to make the young student want to pick up the flyer (eye catching/interesting) and then be motivated to want to self elect - "beg parents" to take up the option. **PLEASE NOTE - I have uploaded a colour swatch now, and would appreciate if desgins could use these colours (not a requirement to use base colours of blue a silver as base if an exciting image needs to come from leaning on "secondary colours" (brighter) as being the predominant colours.
Many thanks, appreciate being able to see such an active community of designers involved in this website
Target Market(s)
1st page; target market 15-19 yr old, looking for young/fresh, exciting, eye catching. same look/feel – target market – parents/person to decide on
Industry/Entity Type
Training
Look and feel

```html
<!DOCTYPE html>
<html lang="en">
<head>
<meta charset="utf-8">
<title>Traineeship Flyer</title>
<link href="https://fonts.googleapis.com/css2?family=Courgette&family=Roboto:wght@400;500;700&family=Kalam:wght@400&family=Lora:ital,wght@1,600&display=swap" rel="stylesheet">
<style>
  :root {
    --navy: #25296b;
    --navy-deep: #1c1f5a;
    --stone: #cbc3b8;
    --ink: #4a4a4a;
    --white: #ffffff;
    --circle: #f3f3f1;
    --step1: #7d8a2a;
    --step2: #8f7424;
    --step3: #9a2a2c;
    --step4: #5c2d91;
    --step5: #2a9340;
    --step6: #2b86ad;
    --photo-a: #6b5a52;
    --photo-b: #b24a5a;
  }
  * { box-sizing: border-box; margin: 0; padding: 0; }
  html, body { width: 1200px; height: 800px; overflow: hidden; background: #e6e6e6; }
  .flyer {
    position: relative; width: 1200px; height: 800px; overflow: hidden;
    background: var(--stone); font-family: "Roboto", sans-serif; color: var(--ink);
  }
  .top-band { position: absolute; left: 0; top: 0; width: 1200px; height: 190px; background: var(--navy); }
  .hero-photo {
    position: absolute; left: 30px; top: 14px; width: 420px; height: 200px;
    border: 5px solid var(--white);
    background: linear-gradient(120deg, var(--photo-a) 0%, #8a7a70 45%, var(--photo-b) 100%);
  }
  .headline {
    position: absolute; left: 500px; top: 40px; width: 660px; text-align: center;
    color: var(--white); font-weight: 700; font-size: 40px; line-height: 1.2;
  }
  .steps { position: absolute; left: 30px; top: 222px; width: 1140px; height: 150px; }
  .step { position: absolute; top: 0; width: 150px; }
  .step-circle {
    width: 140px; height: 110px; border-radius: 50%; background: var(--circle);
    display: flex; align-items: center; justify-content: center; text-align: center;
    font-family: "Kalam", cursive; font-size: 19px; line-height: 1.1; color: #444;
  }
  .step-tag {
    margin: 8px 0 0 40px; width: 120px; padding: 3px 0; border-radius: 4px;
    text-align: center; color: var(--white); font-family: "Lora", serif; font-style: italic;
    font-weight: 600; font-size: 14px;
  }
  .arrow { position: absolute; top: 44px; font-size: 20px; color: #666; }
  .lead {
    position: absolute; left: 40px; top: 388px; font-size: 27px; font-weight: 700; color: #555;
  }
  .question {
    position: absolute; left: 40px; font-family: "Courgette", cursive; font-size: 34px;
    color: var(--navy); padding-bottom: 4px; border-bottom: 1.5px solid var(--navy);
    width: 760px;
  }
  .answer { position: absolute; left: 40px; font-size: 22px; color: #555; }
  .duties { position: absolute; left: 70px; top: 570px; list-style: none; font-size: 20px; color: #555; line-height: 1.55; }
  .duties li { display: flex; align-items: center; gap: 10px; }
  .brace { position: absolute; left: 440px; top: 566px; }
  .side-note { position: absolute; left: 490px; top: 598px; font-size: 24px; color: #555; }
  .bottom-band { position: absolute; left: 0; top: 770px; width: 1200px; height: 30px; background: var(--navy); }
</style>
</head>
<body>
<main class="flyer">
  <div class="top-band"></div>
  <div class="hero-photo" role="img" aria-label="Photo of two electrical trainees in hard hats working on a wiring panel"></div>
  <h1 class="headline">Get ahead of the game<br>Learn on the job</h1>

  <section class="steps">
    <div class="step" style="left:0"><div class="step-circle">Information<br>session</div><div class="step-tag" style="background:var(--step1)">Step 01</div></div>
    <span class="arrow" style="left:150px">&gt;</span>
    <div class="step" style="left:190px"><div class="step-circle">Register<br>your<br>interest</div><div class="step-tag" style="background:var(--step2)">Step 02</div></div>
    <span class="arrow" style="left:340px">&gt;</span>
    <div class="step" style="left:380px"><div class="step-circle">Enrolment</div><div class="step-tag" style="background:var(--step3)">Step 03</div></div>
    <span class="arrow" style="left:530px">&gt;</span>
    <div class="step" style="left:570px"><div class="step-circle">Start<br>training</div><div class="step-tag" style="background:var(--step4)">Step 04</div></div>
    <span class="arrow" style="left:720px">&gt;</span>
    <div class="step" style="left:760px"><div class="step-circle">Practical<br>assessments</div><div class="step-tag" style="background:var(--step5)">Step 05</div></div>
    <span class="arrow" style="left:910px">&gt;</span>
    <div class="step" style="left:950px"><div class="step-circle">Graduate</div><div class="step-tag" style="background:var(--step6)">Step 06</div></div>
  </section>

  <p class="lead">Gain a formal national qualification recognised by all employers Australia wide.</p>

  <h2 class="question" style="top:428px">How much will it cost?</h2>
  <p class="answer" style="top:482px">Nothing! The full course is provided by your employer. No prior training/experience is required.</p>

  <h2 class="question" style="top:514px; top:516px">What would I be expected to do?</h2>
  <ul class="duties">
    <li><svg width="16" height="14" viewBox="0 0 16 14"><path d="M1 7l5 5L15 1" fill="none" stroke="#555" stroke-width="2"/></svg>Earn while your learn</li>
    <li><svg width="16" height="14" viewBox="0 0 16 14"><path d="M1 7l5 5L15 1" fill="none" stroke="#555" stroke-width="2"/></svg>Attend on site training sessions</li>
    <li><svg width="16" height="14" viewBox="0 0 16 14"><path d="M1 7l5 5L15 1" fill="none" stroke="#555" stroke-width="2"/></svg>Online training and assessment</li>
    <li><svg width="16" height="14" viewBox="0 0 16 14"><path d="M1 7l5 5L15 1" fill="none" stroke="#555" stroke-width="2"/></svg>Complete workplace activities</li>
  </ul>
  <svg class="brace" width="40" height="130" viewBox="0 0 40 130">
    <path d="M4 4 C20 4 20 10 20 30 L20 55 C20 62 26 65 36 65 C26 65 20 68 20 75 L20 100 C20 120 20 126 4 126" fill="none" stroke="#333" stroke-width="2.5"/>
  </svg>
  <p class="side-note">All training completed during work hours.</p>

  <h2 class="question" style="top:684px; width:1000px">How long will it take to finish my traineeship?</h2>
  <p class="answer" style="top:738px">If on track, you could complete a Cert II in 6 months if committed to making your training a success.</p>

  <div class="bottom-band"></div>
</main>
</body>
</html>
```